Facebook post - Kestrel Bay Finishes has arrived to make your tiles smile!

Kestrel Bay Finishes would like to release a Facebook post calling out to the market that we have arrived. The company has a new and fresh branding aiming for a female demographic between the ages of 40 and 55 located in the South West of Western Australia. The company image MUST be centered around trust! Our Primary aim is to create an uncompromising trust from the very first impression. Our logo tag line is, 'We love to make your tiles smile'.
I need 5 x facebook template designs and also 5 x posts.
Our 1st campaign is to be 5 x posts centered around the arrival of this fantastic new company.
We are company that provides the services of:
- Grout and silicone repair.
- Broken or drummy tile replacement and;
- Grout sealing
Dont forget that we must communicate TRUST and the Clean lines for tiles that shine!

```html
<!DOCTYPE html>
<html lang="en">
<head>
<meta charset="UTF-8">
<title>Kestrel Bay Finishes – Facebook Post</title>
<link rel="stylesheet" href="https://fonts.googleapis.com/css2?family=Oswald:wght@400&family=Arimo:wght@400&display=swap">
<style>
  :root {
    --brand-blue: #2fa8db;
    --tile-white: #ffffff;
    --grout-line: #e4e5e7;
    --circle-grey: rgba(232, 234, 236, 0.82);
    --text-dark: #3a3a3a;
    --text-grey: #555a5f;
    --on-blue: #ffffff;
  }
  * { margin: 0; padding: 0; box-sizing: border-box; }
  html, body { width: 1200px; height: 1200px; overflow: hidden; background: var(--tile-white); }
  .post {
    position: relative;
    width: 1200px;
    height: 1200px;
    overflow: hidden;
    background: var(--tile-white);
  }
  .tile-grid { position: absolute; inset: 0; }
  .backdrop-circle {
    position: absolute;
    left: 22px; top: 22px;
    width: 1156px; height: 1156px;
    border-radius: 50%;
    background: var(--circle-grey);
  }
  .brand-mark {
    position: absolute;
    left: 550px; top: 310px;
    width: 100px; height: 100px;
    border-radius: 50%;
    background: var(--brand-blue);
  }
  .brand-name {
    position: absolute;
    left: 0; right: 0; top: 500px;
    text-align: center;
    font-family: "Arimo", Arial, sans-serif;
    font-weight: 400;
    font-size: 58px;
    line-height: 1;
    color: var(--brand-blue);
  }
  .tagline {
    position: absolute;
    left: 0; right: 0; top: 566px;
    text-align: center;
    font-family: "Oswald", sans-serif;
    font-size: 22px;
    letter-spacing: 5px;
    text-transform: uppercase;
    color: var(--text-dark);
  }
  .services-box {
    position: absolute;
    left: 191px; top: 656px;
    width: 817px; height: 278px;
    border: 1.5px solid var(--brand-blue);
  }
  .services-heading {
    height: 59px;
    background: var(--brand-blue);
    color: var(--on-blue);
    font-family: "Arimo", Arial, sans-serif;
    font-weight: 400;
    font-size: 43px;
    line-height: 60px;
    padding-left: 98px;
  }
  .services-list {
    list-style: none;
    padding: 24px 0 0 33px;
  }
  .service-item {
    display: flex;
    align-items: center;
    height: 54px;
    font-family: "Arimo", Arial, sans-serif;
    font-size: 40px;
    color: var(--text-grey);
  }
  .service-arrow { width: 48px; height: 36px; margin-right: 12px; flex: none; }
</style>
</head>
<body>
  <main class="post">
    <svg class="tile-grid" width="1200" height="1200" viewBox="0 0 1200 1200" aria-hidden="true">
      <g fill="var(--grout-line)">
        <rect x="246" y="0" width="14" height="1200"/>
        <rect x="593" y="0" width="14" height="1200"/>
        <rect x="940" y="0" width="14" height="1200"/>
        <rect x="0" y="269" width="1200" height="14"/>
        <rect x="0" y="611" width="1200" height="14"/>
        <rect x="0" y="953" width="1200" height="14"/>
      </g>
    </svg>

    <div class="backdrop-circle"></div>

    <div class="brand-mark" aria-hidden="true"></div>
    <h1 class="brand-name">Kestrel Bay Finishes</h1>
    <p class="tagline">Clean lines for tiles that shine!</p>

    <section class="services-box">
      <h2 class="services-heading">We provides the services of</h2>
      <ul class="services-list">
        <li class="service-item">
          <svg class="service-arrow" viewBox="0 0 48 36" aria-hidden="true"><path d="M0 10h26V0l22 18-22 18V26H0z" fill="var(--brand-blue)"/></svg>
          Grout and silicone repair.
        </li>
        <li class="service-item">
          <svg class="service-arrow" viewBox="0 0 48 36" aria-hidden="true"><path d="M0 10h26V0l22 18-22 18V26H0z" fill="var(--brand-blue)"/></svg>
          Broken or drummy tile replacement
        </li>
        <li class="service-item">
          <svg class="service-arrow" viewBox="0 0 48 36" aria-hidden="true"><path d="M0 10h26V0l22 18-22 18V26H0z" fill="var(--brand-blue)"/></svg>
          Grout sealing
        </li>
      </ul>
    </section>
  </main>
</body>
</html>
```